Business card design for holistic health care clinic

We need a double-sided business card design for our holistic health care clinic that integrates our logo design and also its color scheme. My business is called Valmira. It is an integrative medicine clinic. You have already done the logo for me. Please ensure an elegant and upscale design that is not cluttered, but still has all the necessary information (please see below for details).

Target Market(s)

Wellness, fitness, rehabilitation for educated, well-traveled open-minded clients who are focused on natural, organic, balanced and preventive healthcare and lifestyle.

Industry/Entity Type

Medical

Contact Information for Business Card

Modern, clean.

Number of Pages Required

1 page

Font styles to use
Serif
Sans Serif

Colors

Designer to choose colors to be used in the design.

Requirements
Must have
• Logo on one side, all other information on the other side.
• Other information should include:
• Tobias Wrenfeld - DOE, CPT, LMT
• 4100 East Marrow Drive
• Austin, TX 78119
• 512 555 0148
• 818 555 0192
• info@ValmiraHealth.example
• t.wrenfeld@ValmiraHealth.example
Nice to have
• Darker background on front - but not totally black - shaded/dark gray.

```html
<!DOCTYPE html>
<html lang="en">
<head>
<meta charset="utf-8">
<title>Valmira business cards</title>
<link href="https://fonts.googleapis.com/css2?family=Nunito:wght@400;700;800&display=swap" rel="stylesheet">
<style>
  :root {
    --stage: #2b2b2b;
    --brand-blue: #1a8fd0;
    --card-gray: #a6a6a6;
    --card-white: #f1f1f1;
    --ink-on-gray: #ffffff;
    --ink-on-white: #4a4a4a;
    --divider-gray: #cfcfcf;
    --divider-white: #c9c9c9;
  }
  * { box-sizing: border-box; margin: 0; padding: 0; }
  html, body { width: 1200px; height: 961px; overflow: hidden; }
  body {
    background: var(--stage);
    font-family: "Nunito", sans-serif;
    position: relative;
  }
  .card {
    position: absolute;
    width: 452px;
    height: 258px;
    overflow: hidden;
    box-shadow: 0 2px 6px rgba(0,0,0,.45);
  }
  .card--gray { background: var(--card-gray); color: var(--ink-on-gray); }
  .card--white { background: var(--card-white); color: var(--ink-on-white); }
  .pos-front-gray { left: 134px; top: 206px; }
  .pos-front-white { left: 617px; top: 206px; }
  .pos-back-white { left: 132px; top: 496px; }
  .pos-back-gray { left: 615px; top: 496px; }

  .brand-name {
    position: absolute;
    color: var(--brand-blue);
    font-weight: 800;
    letter-spacing: 0.5px;
    text-align: center;
    line-height: 1;
  }
  .card-front .brand-name { left: 30px; width: 176px; top: 102px; font-size: 40px; }
  .card-back .brand-name { left: 0; width: 100%; top: 102px; font-size: 56px; }

  .divider {
    position: absolute;
    left: 236px; top: 47px;
    width: 1px; height: 127px;
  }
  .card--gray .divider { background: var(--divider-gray); }
  .card--white .divider { background: var(--divider-white); }

  .contact { position: absolute; left: 256px; top: 51px; }
  .contact-name {
    color: var(--brand-blue);
    font-weight: 800;
    font-size: 15.5px;
    line-height: 1;
    letter-spacing: 0.2px;
  }
  .contact-title {
    color: var(--brand-blue);
    font-weight: 700;
    font-size: 9px;
    margin-top: 2px;
    letter-spacing: 0.3px;
  }
  .contact-address {
    font-size: 11px;
    line-height: 13px;
    margin-top: 9px;
  }
  .contact-list { list-style: none; margin-top: 5px; }
  .contact-list li {
    display: flex;
    align-items: center;
    font-size: 11px;
    line-height: 14.5px;
  }
  .contact-list svg { width: 10px; height: 10px; margin-right: 6px; flex: none; }
  .icon { fill: var(--brand-blue); }

  .tagline-band {
    position: absolute;
    left: 0; top: 220px;
    width: 100%; height: 17px;
    background: var(--brand-blue);
    color: #ffffff;
    font-size: 10px;
    font-weight: 700;
    line-height: 17px;
    padding-left: 36px;
  }
</style>
</head>
<body>

  <section class="card card--gray card-front pos-front-gray">
    <div class="brand-name">Valmira</div>
    <div class="divider"></div>
    <div class="contact">
      <div class="contact-name">TOBIAS WRENFELD</div>
      <div class="contact-title">DOE, CPT, LMT</div>
      <div class="contact-address">4100 East Marrow Drive<br>Austin, TX 78119</div>
      <ul class="contact-list">
        <li><svg viewBox="0 0 10 10"><path class="icon" d="M2 0.5 L3.6 2.8 L2.8 3.8 Q4 6 6.2 7.2 L7.2 6.4 L9.5 8 L8.4 9.5 Q4.5 9 1.5 5.5 Q0.3 3.5 0.5 1.6 Z"/></svg>512 555 0148</li>
        <li><svg viewBox="0 0 10 10"><rect class="icon" x="2.5" y="0" width="5" height="10" rx="1"/><rect x="3.3" y="1.2" width="3.4" height="6.6" fill="#fff"/></svg>818 555 0192</li>
        <li><svg viewBox="0 0 10 10"><rect class="icon" x="0" y="2" width="10" height="6.5"/><path d="M0 2 L5 5.8 L10 2" stroke="#fff" stroke-width="0.9" fill="none"/></svg>t.wrenfeld@ValmiraHealth.example</li>
        <li><svg viewBox="0 0 10 10"><circle class="icon" cx="5" cy="5" r="4.8"/><path d="M5 0.5 V9.5 M0.5 5 H9.5" stroke="#fff" stroke-width="0.7"/></svg>www.ValmiraHealth.example</li>
      </ul>
    </div>
    <div class="tagline-band">At Valmira, it’s all about you – your health, your objectives</div>
  </section>

  <section class="card card--white card-front pos-front-white">
    <div class="brand-name">Valmira</div>
    <div class="divider"></div>
    <div class="contact">
      <div class="contact-name">TOBIAS WRENFELD</div>
      <div class="contact-title">DOE, CPT, LMT</div>
      <div class="contact-address">4100 East Marrow Drive<br>Austin, TX 78119</div>
      <ul class="contact-list">
        <li><svg viewBox="0 0 10 10"><path class="icon" d="M2 0.5 L3.6 2.8 L2.8 3.8 Q4 6 6.2 7.2 L7.2 6.4 L9.5 8 L8.4 9.5 Q4.5 9 1.5 5.5 Q0.3 3.5 0.5 1.6 Z"/></svg>512 555 0148</li>
        <li><svg viewBox="0 0 10 10"><rect class="icon" x="2.5" y="0" width="5" height="10" rx="1"/><rect x="3.3" y="1.2" width="3.4" height="6.6" fill="#f1f1f1"/></svg>818 555 0192</li>
        <li><svg viewBox="0 0 10 10"><rect class="icon" x="0" y="2" width="10" height="6.5"/><path d="M0 2 L5 5.8 L10 2" stroke="#f1f1f1" stroke-width="0.9" fill="none"/></svg>t.wrenfeld@ValmiraHealth.example</li>
        <li><svg viewBox="0 0 10 10"><circle class="icon" cx="5" cy="5" r="4.8"/><path d="M5 0.5 V9.5 M0.5 5 H9.5" stroke="#f1f1f1" stroke-width="0.7"/></svg>www.ValmiraHealth.example</li>
      </ul>
    </div>
    <div class="tagline-band">At Valmira, it’s all about you – your health, your objectives</div>
  </section>

  <section class="card card--white card-back pos-back-white">
    <div class="brand-name">Valmira</div>
  </section>

  <section class="card card--gray card-back pos-back-gray">
    <div class="brand-name">Valmira</div>
  </section>

</body>
</html>
```